Business Card design for insurance broker in Denver, CO, USA

I need a business card designed using this logo that was just created. We sell life and disability income insurance to US consumers.
Looking for a professionally designed card to make use of the logo and have something to hand to prospects or new business referral sources. The card could be white, gray, black or whatever you would recommend.

Target Market(s)

US Consumers and other financial professionals that I partner with.

Industry/Entity Type

Insurance Broker

Contact Information for Business Card

Owen T. Farrow, CLU, LUTCF (please note that CLU should have a superscript R in a circle for registered trademark)
President
phone (303) 555-0187
email owen@keelbrookcover.example
4620 W. Halvern Rd, Suite 300, Ashcombe Ridge, CO 80999
Somewhere fit in a tagline saying "Your resource for life, long term care, and disability insurance" (maybe the back if it doesn't fit on the front, your call)

Font styles to use
Sans Serif

Requirements
Must have
• Must have logo in correct blue and gray colors, my name, address, phone, email. Order and placement determined by the designer.
• I just want something that looks a more professional than what I could have done using the business card designer tool on pixelbazaar.example or QuillPress, or any other do-it-yourself tool
• A regular rectangular business card with square corners is preferred
Nice to have
• I included the logos of 2 organizations I belong to (GKLS and WOBCE). They should be small, but visible on the back only. If it doesn’t look good, this is not a requirement, feel free to drop it.
Should not have
• Do not add any colors not already in the logo, except use of black and whites which are okay. If you use the logo on the back and want to make that in all black, gray or white, that may be okay as well.

```html
<!DOCTYPE html>
<html lang="en">
<head>
<meta charset="utf-8">
<title>Keelbrook Cover – Business Card</title>
<link href="https://fonts.googleapis.com/css2?family=Arimo:wght@400;700&family=Lato:wght@400;700&display=swap" rel="stylesheet">
<style>
  :root {
    --brand-blue: #2386c8;
    --brand-gray: #a3a3a3;
    --ink: #1d1d1f;
    --paper: #ffffff;
    --backdrop: #c4c4c6;
  }
  * { margin: 0; padding: 0; box-sizing: border-box; }
  html, body { width: 1200px; height: 820px; overflow: hidden; }
  body { background: var(--backdrop); position: relative; }

  .card {
    position: absolute;
    width: 529px;
    height: 313px;
    overflow: hidden;
  }
  .card-arcs { position: absolute; left: 0; top: 0; }

  /* Front */
  .card-front { left: 62px; top: 277px; background: var(--brand-blue); font-family: "Arimo", sans-serif; }
  .brand { position: absolute; left: 27px; top: 50px; display: flex; align-items: center; }
  .brand-dot { width: 98px; height: 98px; border: 4px solid var(--paper); border-radius: 50%; }
  .brand-divider { width: 2px; height: 100px; background: var(--brand-gray); margin: 0 10px 0 10px; }
  .brand-name { color: var(--paper); font-weight: 700; font-size: 34px; line-height: 30px; letter-spacing: 0.2px; }
  .tagline { position: absolute; left: 35px; top: 229px; color: var(--paper); font-size: 17.5px; line-height: 21.5px; }
  .front-stripe { position: absolute; left: 0; right: 0; top: 293px; height: 6px; background: var(--paper); }

  /* Back */
  .card-back { left: 619px; top: 278px; background: var(--paper); font-family: "Lato", sans-serif; }
  .memberships { position: absolute; right: 20px; top: 28px; display: flex; gap: 14px; align-items: center; }
  .person { position: absolute; right: 27px; top: 151px; text-align: right; }
  .person-name { font-size: 25px; font-weight: 700; color: var(--ink); line-height: 1.1; }
  .person-name .given { color: var(--brand-blue); }
  .person-name sup { font-size: 13px; color: var(--brand-blue); font-weight: 400; }
  .person-role { font-size: 20px; color: var(--brand-gray); margin-top: 4px; }
  .contact { position: absolute; left: 0; right: 27px; top: 235px; display: flex; justify-content: flex-end; align-items: stretch; font-size: 13.5px; color: var(--ink); line-height: 19px; }
  .contact-lines { text-align: right; padding-right: 10px; border-right: 2px solid var(--brand-gray); }
  .contact-lines .label { color: var(--brand-blue); }
  .address { text-align: center; padding: 0 8px 0 10px; border-right: 2px solid var(--brand-blue); }
  .back-band { position: absolute; left: 0; right: 0; background: var(--brand-blue); }
  .back-band.upper { top: 284px; height: 9px; }
  .back-band.lower { top: 301px; height: 12px; }
</style>
</head>
<body>
  <section class="card card-front" aria-label="Card front">
    <svg class="card-arcs" width="529" height="313" aria-hidden="true">
      <circle cx="540" cy="145" r="113" fill="none" stroke="var(--paper)" stroke-width="7"/>
      <path d="M 476 64 A 110 110 0 0 1 529 38" fill="none" stroke="var(--brand-gray)" stroke-width="5"/>
    </svg>
    <div class="brand">
      <div class="brand-dot"></div>
      <div class="brand-divider"></div>
      <div class="brand-name">KEELBROOK<br>COVER</div>
    </div>
    <p class="tagline">Your resource for life,<br>long term care, and disability insurance</p>
    <div class="front-stripe"></div>
  </section>

  <section class="card card-back" aria-label="Card back">
    <svg class="card-arcs" width="529" height="313" aria-hidden="true">
      <circle cx="-2" cy="143" r="97" fill="none" stroke="var(--brand-gray)" stroke-width="15"/>
      <path d="M 0 267 A 124 124 0 0 0 95 203" fill="none" stroke="var(--brand-blue)" stroke-width="4"/>
      <path d="M 0 26 A 124 124 0 0 1 15 28" fill="none" stroke="var(--brand-blue)" stroke-width="2"/>
    </svg>
    <div class="memberships">
      <svg width="70" height="50" role="img" aria-label="WOBCE membership badge">
        <polygon points="35,4 66,46 4,46" fill="var(--brand-blue)"/>
      </svg>
      <svg width="50" height="50" role="img" aria-label="GKLS membership badge">
        <circle cx="25" cy="25" r="21" fill="none" stroke="var(--brand-blue)" stroke-width="4"/>
      </svg>
    </div>

    <div class="person">
      <h1 class="person-name"><span class="given">Owen T. Farrow</span>, CLU<sup>®</sup>, LUTCF</h1>
      <p class="person-role">President</p>
    </div>

    <div class="contact">
      <div class="contact-lines">
        <p><span class="label">P:</span> (303) 555-0187</p>
        <p><span class="label">E:</span> owen@keelbrookcover.example</p>
      </div>
      <div class="address">
        <p>4620 W. Halvern Rd, Suite 300,</p>
        <p>Ashcombe Ridge, CO 80999</p>
      </div>
    </div>

    <div class="back-band upper"></div>
    <div class="back-band lower"></div>
  </section>
</body>
</html>
```